Web Design job - Condo Debts Collection Business needs a Web Design

I need a site for a client, who works with condo debts collection, and ensure all revenues provided by condo fees will be always available to the building manager of condo on a specific date, regardless of defaults.
I have the visual identity (logo, slogan and colors) of the company, and some requirements on layout (kind of slider, menu options, phone number on a noble position, etc) - maybe I can do a sketch, but I like the idea of give some freedom to designer.

*** PLEASE, we have no interest in templates. We want something new***

Target Market(s)

I have two targets for this design: - Condominium's building manager. This target is looking for a solution to overdue debts on it's condo. - Residents on condominiums. This target wants to live in a better place, where their neighbors pay their condominium fees on time.

Number of Pages Required

1 page

Requirements
Must have
• - Slider with title, some short text related, a nice image (I prefer happy and/or peaceful family, people doing business, happy friends, and so on).
• - I have a special attention to menu. I'm looking for one I can have a nice effect, more elegant, charming, kind of innovative.
• - Phone number on the top (or clearly visible).
• - Member log in area or icon on the top (or clearly visible).
• - News/articles area.
• - Modern fonts, with good quality, sans-serif on areas where reading is more intensive (prefer Google web-fonts).
• - Colors specified on attached files.
Nice to have
• - Clear background color, cause it's better to read larger texts (like articles). Dark backgrounds makes reading difficult.
• - A site with effects (like shadows, lines, curves, gradients, lights) is usually pretty.
• - I pay attention on beautiful footers.
Should not have
• - Images with a lot of money (I don't sell richness, I sell tranquility, peace, harmony, safety).
• - Poor menu.

```html
<!DOCTYPE html>
<html lang="en">
<head>
<meta charset="utf-8">
<title>Condara – Condo Fee Collection</title>
<link rel="stylesheet" href="https://fonts.googleapis.com/css2?family=Raleway:wght@300;400;600;700&family=Roboto+Slab:wght@300;400;700&display=swap">
<style>
:root{
  --yellow:#e6ad1b;
  --yellow-dark:#d39a12;
  --yellow-light:#f3c640;
  --ink:#2e2e2e;
  --body:#4a4a4a;
  --muted:#8a8a8a;
  --grey-band:#ececec;
  --line:#dedede;
  --white:#ffffff;
}
*{box-sizing:border-box;margin:0;padding:0}
html,body{width:1200px;height:3629px;overflow:hidden}
body{position:relative;background:var(--white);font-family:"Roboto Slab",serif;color:var(--body)}
.abs{position:absolute}
h1,h2,h3{font-family:"Raleway",sans-serif;font-weight:300;color:var(--ink)}

/* header */
.topbar{left:690px;top:0;width:440px;height:34px;background:var(--yellow);border-radius:0 0 0 24px;display:flex;align-items:center;justify-content:space-around;color:#fff;font-size:12px;letter-spacing:.5px}
.topbar span{display:flex;align-items:center;gap:7px}
.brand{left:160px;top:26px;display:flex;align-items:center;gap:12px}
.brand-mark{width:44px;height:44px;background:var(--yellow)}
.brand-name{font-family:"Raleway",sans-serif;font-weight:700;font-size:42px;color:var(--ink);line-height:1}
.nav{left:418px;top:68px;display:flex;gap:0;font-family:"Roboto Slab",serif;font-size:15px;color:var(--ink)}
.nav a{display:block;padding:6px 20px;color:inherit;text-decoration:none;border-radius:16px}
.nav a.active{background:var(--yellow);color:var(--ink);font-weight:700}
.nav .caret{color:var(--yellow);font-size:10px;margin-left:4px}

/* hero */
.hero{left:0;top:114px;width:1200px;height:596px;background:linear-gradient(115deg,#6b5a4a 0%,#8c7560 40%,#c9a55a 75%,#e6ad1b 100%);clip-path:polygon(0 0,100% 0,100% 83%,0 100%)}
.hero-title{left:160px;top:306px;font-size:44px;color:#fff;font-weight:300}
.hero-sub{left:160px;top:372px;width:430px;font-size:20px;line-height:30px;color:#fff}
.dots{left:566px;top:630px;display:flex;gap:7px}
.dots i{width:11px;height:11px;border-radius:50%;background:#fff;display:block}
.dots i.on{background:var(--yellow)}

/* buttons */
.btn{display:inline-block;height:30px;padding:0 22px;line-height:28px;border-radius:15px;font-size:10px;font-weight:700;letter-spacing:.5px;text-transform:uppercase;border:1.5px solid var(--yellow);color:var(--yellow);background:#fff}
.btn.fill{background:var(--yellow);color:#fff}

/* about */
.about-photo{left:160px;top:765px;width:474px;height:329px;border:4px solid var(--yellow);background:linear-gradient(135deg,#e9e3d8,#b9a48a 60%,#6f5b48)}
.about-title{left:675px;top:776px;font-size:46px}
.about-text{left:678px;top:846px;width:362px;font-size:11px;line-height:20.5px;color:var(--body)}
.about .btn{position:absolute;left:678px;top:1038px}

/* what we do */
.band{left:0;top:1137px;width:1200px;height:650px;background:var(--grey-band);clip-path:polygon(0 12%,100% 0,100% 88%,0 100%)}
.section-title{width:1200px;left:0;text-align:center;font-size:46px}
.services{left:162px;top:1355px;display:flex;gap:16px}
.card{width:206px;height:296px;background:#fff;border:1px solid var(--line);text-align:center;padding-top:38px}
.card.active{border-bottom:4px solid var(--yellow)}
.card svg{width:82px;height:64px}
.card h3{font-size:15px;margin-top:40px;letter-spacing:.5px;font-weight:400;color:var(--ink)}
.card p{font-size:10px;line-height:16px;margin:8px 24px 0;color:var(--body)}
.card .btn{margin-top:14px}

/* news */
.news{left:160px;top:1934px;display:grid;grid-template-columns:repeat(3,276px);column-gap:27px;row-gap:0}
.post{height:389px;position:relative}
.post-photo{height:162px;position:relative}
.post-photo::after{content:"";position:absolute;left:0;bottom:0;width:0;height:0;border-left:24px solid #fff;border-right:60px solid transparent;border-top:0}
.post-meta{margin-top:22px;font-size:10px;color:var(--yellow);font-weight:700;display:flex;gap:28px}
.post h3{font-size:19px;margin-top:6px;font-weight:400}
.post p{font-size:10px;line-height:17px;margin-top:8px;color:var(--body)}
.post .btn{margin-top:20px}

/* contact */
.contact{left:0;top:2771px;width:1200px;height:520px;background:linear-gradient(180deg,var(--yellow-light) 0%,var(--yellow) 60%,var(--yellow-dark) 100%);clip-path:polygon(0 0,100% 12%,100% 100%,0 100%)}
.contact-photo{left:560px;top:2771px;width:640px;height:520px;background:radial-gradient(circle at 50% 55%,rgba(170,120,70,.35),rgba(230,173,27,0) 70%);clip-path:polygon(0 0,100% 12%,100% 100%,0 100%)}
.contact-title{left:160px;top:2868px;font-size:46px;color:#fff}
.contact-intro{left:160px;top:2950px;width:440px;font-size:10px;line-height:18px;color:#fff}
.contact-line{left:160px;display:flex;gap:24px;color:#fff;font-size:12px;line-height:20px}
.contact-line svg{flex:none;width:20px;height:20px}
.form{left:719px;top:2807px;width:321px;height:412px;background:#fff;box-shadow:0 6px 18px rgba(0,0,0,.2);padding:30px 27px}
.form h2{text-align:center;font-size:28px;margin-bottom:14px}
.field{height:28px;border:1px solid var(--line);margin-bottom:7px;display:flex;align-items:center;gap:8px;padding-left:8px;font-size:10px;color:var(--muted)}
.field i{width:14px;height:14px;border-radius:50%;border:1px solid #bbb;display:block}
.field.area{height:102px;align-items:flex-start;padding-top:7px}
.send{height:30px;background:var(--yellow);color:#fff;text-align:center;line-height:30px;font-size:13px;font-weight:700;letter-spacing:.5px}

/* footer */
.footer-wave{left:0;top:3420px;width:1200px;height:209px}
.footer-brand{left:160px;top:3360px;display:flex;align-items:center;gap:10px}
.footer-brand .brand-mark{width:34px;height:34px}
.footer-brand .brand-name{font-size:34px}
.footer-about{left:160px;top:3425px;width:240px;font-size:10px;line-height:17px}
.fcol{font-size:10px;line-height:26px;color:var(--ink)}
.fcol h4{font-family:"Raleway",sans-serif;font-weight:400;font-size:17px;margin-bottom:6px;color:var(--ink)}
.social{display:flex;gap:12px;align-items:center;margin:4px 0 18px}
.social i{width:22px;height:22px;background:var(--ink);display:block;border-radius:50%}
.copy{left:0;width:1200px;top:3574px;text-align:center;font-size:11px;color:var(--body)}
</style>
</head>
<body>

<header>
  <div class="abs topbar">
    <span><svg width="12" height="12" viewBox="0 0 12 12"><circle cx="6" cy="3.5" r="2.7" fill="#fff"/><path d="M1 12c0-3 2.2-5 5-5s5 2 5 5z" fill="#fff"/></svg>MEMBER LOG IN</span>
    <span><svg width="12" height="12" viewBox="0 0 24 24"><path d="M6.6 10.8a15 15 0 006.6 6.6l2.2-2.2c.3-.3.7-.4 1-.2 1.1.4 2.3.6 3.6.6.6 0 1 .4 1 1V20c0 .6-.4 1-1 1A17 17 0 013 4c0-.6.4-1 1-1h3.5c.6 0 1 .4 1 1 0 1.3.2 2.5.6 3.6.1.3 0 .7-.2 1z" fill="#fff"/></svg>Phone: (55) 555 0142</span>
  </div>
  <div class="abs brand"><span class="brand-mark"></span><span class="brand-name">condara</span></div>
  <nav class="abs nav">
    <a class="active" href="#">Home</a>
    <a href="#">About</a>
    <a href="#">Services<span class="caret">▼</span></a>
    <a href="#">Why Choose us?</a>
    <a href="#">Faq</a>
    <a href="#">Contact Us</a>
  </nav>
</header>

<section class="hero-wrap">
  <div class="abs hero" role="img" aria-label="Happy family relaxing together at home"></div>
  <h1 class="abs hero-title">Welcome to Condara</h1>
  <p class="abs hero-sub">Sed ut perspiciatis unde omniste natus error sit volupiat istarspis und.</p>
  <div class="abs dots"><i></i><i></i><i></i><i class="on"></i></div>
</section>

<section class="about">
  <div class="abs about-photo" role="img" aria-label="Advisor reviewing documents with a couple"></div>
  <h2 class="abs about-title">About Company</h2>
  <p class="abs about-text">Sed ut perspiciatis unde omnis iste natus error sit voluptatem accusa ntium doloremque laudantium, totam rem aperiam, eaque ipsa quae ab illo inventore veritatis et quasi architecto beatae vitae dicta sunt ex pli cabo nemo enim ipsam voluptatem quia voluptas sit aspernatur aut odit aut fugit sed quia consequuntur magni dolores eos qui ratione volup tatem sequi nesciunt neque porro quisquam est qui dolorem ipsum quia dolor sit amet consectetur adipisci velit sed quia non numquam eius modi tempora incidunt ut labore et dolore magnam aliquam quaerat.</p>
  <a class="btn fill" href="#">Read More</a>
</section>

<section class="what">
  <div class="abs band"></div>
  <h2 class="abs section-title" style="top:1258px">What We Do</h2>
  <div class="abs services">
    <div class="card active">
      <svg viewBox="0 0 82 64" fill="none" stroke="#e6ad1b" stroke-width="2"><path d="M10 30L41 6l31 24"/><path d="M18 24v34h46V24"/><rect x="34" y="38" width="14" height="20"/><rect x="24" y="30" width="8" height="8"/><rect x="50" y="30" width="8" height="8"/><path d="M4 58h74"/></svg>
      <h3>SERSPICIATND</h3>
      <p>Seciatis unde omnis iste natt voluptatem accusantium doloreque audantium, totam remlo.</p>
      <a class="btn fill" href="#">Read More</a>
    </div>
    <div class="card">
      <svg viewBox="0 0 82 64" fill="none" stroke="#e6ad1b" stroke-width="2"><path d="M16 20l36-12 4 12"/><rect x="14" y="20" width="54" height="36" rx="3"/><path d="M52 32h18v12H52a6 6 0 010-12z"/><circle cx="55" cy="38" r="2"/></svg>
      <h3>SERSPICIATND</h3>
      <p>Seciatis unde omnis iste natt voluptatem accusantium doloreque audantium, totam remlo.</p>
      <a class="btn" href="#">Read More</a>
    </div>
    <div class="card">
      <svg viewBox="0 0 82 64" fill="none" stroke="#e6ad1b" stroke-width="2"><path d="M18 26L41 8l23 18"/><path d="M24 22v14M58 22v14"/><circle cx="41" cy="34" r="7"/><path d="M28 58c0-8 6-13 13-13s13 5 13 13z"/><rect x="46" y="12" width="8" height="6"/></svg>
      <h3>SERSPICIATND</h3>
      <p>Seciatis unde omnis iste natt voluptatem accusantium doloreque audantium, totam remlo.</p>
      <a class="btn" href="#">Read More</a>
    </div>
    <div class="card">
      <svg viewBox="0 0 82 64" fill="none" stroke="#e6ad1b" stroke-width="2"><path d="M26 22L44 8l18 14"/><path d="M30 19v16h28V19"/><rect x="40" y="26" width="8" height="9"/><path d="M8 44h10l10 6h14a3 3 0 010 6H28"/><path d="M42 56l22-8a4 4 0 013 7L46 62H18"/></svg>
      <h3>SERSPICIATND</h3>
      <p>Seciatis unde omnis iste natt voluptatem accusantium doloreque audantium, totam remlo.</p>
      <a class="btn" href="#">Read More</a>
    </div>
  </div>
</section>

<section class="news-wrap">
  <h2 class="abs section-title" style="top:1826px">News/Articles</h2>
  <div class="abs news">
    <article class="post">
      <div class="post-photo" role="img" aria-label="Agent handing house keys to a couple" style="background:linear-gradient(135deg,#cdd6df,#8fa0b0 60%,#4d5a68)"></div>
      <div class="post-meta"><span>JULY 10, 2018</span><span>0 COMMENTS</span></div>
      <h3>Sed ut perspiciatis mnis is</h3>
      <p>Sed ut perspiciatis unde os istenatus error sit vol uptatem accutium doloremque laudantiset ut per spiciatis unde os istenatus error sit vo.</p>
      <a class="btn fill" href="#">Read More</a>
    </article>
    <article class="post">
      <div class="post-photo" role="img" aria-label="Business meeting in a bright office" style="background:linear-gradient(135deg,#e8e6e2,#b3aca2 60%,#5a5048)"></div>
      <div class="post-meta"><span>JULY 10, 2018</span><span>0 COMMENTS</span></div>
      <h3>Accumsan massa</h3>
      <p>Sed ut perspiciatis unde os istenatus error sit vol uptatem accutium doloremque laudantiset ut per spiciatis unde os istenatus error sit vo.</p>
      <a class="btn" href="#">Read More</a>
    </article>
    <article class="post">
      <div class="post-photo" role="img" aria-label="Brick apartment building under blue sky" style="background:linear-gradient(180deg,#3a74c6,#7ea7dc 45%,#9a5a3e 70%,#6b3d2b)"></div>
      <div class="post-meta"><span>JULY 10, 2018</span><span>0 COMMENTS</span></div>
      <h3>Sed ut perspiciatisnis is</h3>
      <p>Sed ut perspiciatis unde os istenatus error sit vol uptatem accutium doloremque laudantiset ut per spiciatis unde os istenatus error sit vo.</p>
      <a class="btn" href="#">Read More</a>
    </article>
    <article class="post">
      <div class="post-photo" role="img" aria-label="Team working around a table with papers" style="background:linear-gradient(135deg,#2f4a68,#5f6f7a 50%,#a08664)"></div>
      <div class="post-meta"><span>JULY 10, 2018</span><span>0 COMMENTS</span></div>
      <h3>Sed ut perspiciatis mnis is</h3>
      <p>Sed ut perspiciatis unde os istenatus error sit vol uptatem accutium doloremque laudantiset ut per spiciatis unde os istenatus error sit vo.</p>
      <a class="btn" href="#">Read More</a>
    </article>
    <article class="post">
      <div class="post-photo" role="img" aria-label="Modern residential tower with balconies" style="background:linear-gradient(180deg,#c9d4dc,#8c939a 50%,#4e4a46)"></div>
      <div class="post-meta"><span>JULY 10, 2018</span><span>0 COMMENTS</span></div>
      <h3>Accumsan massa</h3>
      <p>Sed ut perspiciatis unde os istenatus error sit vol uptatem accutium doloremque laudantiset ut per spiciatis unde os istenatus error sit vo.</p>
      <a class="btn" href="#">Read More</a>
    </article>
    <article class="post">
      <div class="post-photo" role="img" aria-label="Senior couple reviewing paperwork with an advisor" style="background:linear-gradient(135deg,#dfe3e6,#a7b0b6 55%,#4f5a66)"></div>
      <div class="post-meta"><span>JULY 10, 2018</span><span>0 COMMENTS</span></div>
      <h3>Sed ut perspiciatisnis is</h3>
      <p>Sed ut perspiciatis unde os istenatus error sit vol uptatem accutium doloremque laudantiset ut per spiciatis unde os istenatus error sit vo.</p>
      <a class="btn" href="#">Read More</a>
    </article>
  </div>
</section>

<section class="contact-wrap">
  <div class="abs contact"></div>
  <div class="abs contact-photo" role="img" aria-label="Friends laughing together, tinted in yellow"></div>
  <h2 class="abs contact-title">Contact Us</h2>
  <p class="abs contact-intro">Sed ut perspiciatis unde os istenatus error sit voluptatem accutium doloremque lau dantiset ut perspiciatis unde os istenatus error sit vo.</p>
  <div class="abs contact-line" style="top:3018px">
    <svg viewBox="0 0 20 20" fill="none" stroke="#fff" stroke-width="1.5"><path d="M10 19s-6-6.5-6-11a6 6 0 0112 0c0 4.5-6 11-6 11z"/><circle cx="10" cy="8" r="2.2"/></svg>
    <span>Rua das Acácias, 220 Sala 310, Ed. Horizonte,<br>CEP: 00.000-000, Centro, Vila Serena-CE</span>
  </div>
  <div class="abs contact-line" style="top:3104px">
    <svg viewBox="0 0 24 24" fill="none" stroke="#fff" stroke-width="1.5"><path d="M6.6 10.8a15 15 0 006.6 6.6l2.2-2.2c.3-.3.7-.4 1-.2 1.1.4 2.3.6 3.6.6.6 0 1 .4 1 1V20c0 .6-.4 1-1 1A17 17 0 013 4c0-.6.4-1 1-1h3.5c.6 0 1 .4 1 1 0 1.3.2 2.5.6 3.6.1.3 0 .7-.2 1z"/></svg>
    <span>Phone: (55) 555 0142</span>
  </div>
  <div class="abs contact-line" style="top:3164px">
    <svg viewBox="0 0 20 20" fill="none" stroke="#fff" stroke-width="1.5"><rect x="1.5" y="4" width="17" height="12"/><path d="M1.5 4l8.5 7 8.5-7"/></svg>
    <span>contato@condara.example</span>
  </div>
  <form class="abs form">
    <h2>Contact Form</h2>
    <div class="field"><i></i>Name</div>
    <div class="field"><i></i>Email</div>
    <div class="field"><i></i>Phone</div>
    <div class="field"><i></i>Company</div>
    <div class="field area"><i></i>Subject</div>
    <div class="send">SEND</div>
  </form>
</section>

<footer>
  <svg class="abs footer-wave" viewBox="0 0 1200 209" preserveAspectRatio="none"><path d="M0 90C200 30 380 150 620 80S980 40 1200 110V209H0z" fill="#f1f2f6"/><path d="M0 140C260 90 420 190 700 130S1020 120 1200 160V209H0z" fill="#e9ebf1"/></svg>
  <div class="abs footer-brand"><span class="brand-mark"></span><span class="brand-name">condara</span></div>
  <p class="abs footer-about">Sed ut perspiciatis unde omnis iste nas error sit voluptatem accu dolorese laudan tium, totam rem aperiam, eaque ipsa uae a biloatis et quas.</p>
  <div class="abs fcol" style="left:494px;top:3350px">
    <h4>Links</h4>
    <div>Sed uerspiciatis</div><div>Commitetuunt</div><div>Sed uerspiciatis</div><div>Commitetuunt</div><div>Perspiciatis unde</div>
  </div>
  <div class="abs fcol" style="left:709px;top:3350px">
    <h4>Connect</h4>
    <div class="social">
      <svg width="24" height="18" viewBox="0 0 24 18"><rect width="24" height="18" fill="#2e2e2e"/><path d="M0 0l12 9 12-9" fill="none" stroke="#fff" stroke-width="1.5"/></svg>
      <i></i><i></i><i></i>
    </div>
    <h4>Policies</h4>
    <div>Privacy</div><div>Complaint and Feedback</div>
  </div>
  <div class="abs fcol" style="left:925px;top:3350px">
    <h4>Other Links</h4>
    <div>Sed uerspiciatis</div><div>Sed uerspiciatis</div><div>Commitetuunt</div><div>Perspiciatis unde</div><div>Sed uerspiciatis</div>
  </div>
  <p class="abs copy">© 2018 Condara. All Rights are Reserved. Privacy Policy | Terms of Use | Contact</p>
</footer>

</body>
</html>
```